Website for Plumbing Company, Mr. FlowKettle

I need a 7-page fully HTML-coded website for my plumbing company, Mr. FlowKettle. We specialize in installation, repair, and replacement of both gas and electric water heaters. Although we offer both tankless (on-demand) water heaters and standard (with tank) water heaters, most of our business is related to standard (with tank) water heaters in the USA market.

These are the pages I need:
1. Home page with sections such as About Us, Our Services, Why Choose Us, Testimonials, Location Map (Palm Beach County Florida), Quote Request Form, Join Our Newsletter, Mission Statement, etc.

2. Gas Water Heaters

3. Electric Water Heaters

4. Tankless Water Heaters

5. About Us

6. Contact Us

7. Privacy Policy, Terms & Conditions

Be sure to mention the following points:
1. Same-Day Service
2. Best Price Guarantee
3. 100% Satisfaction Rating
4. 15-Year Warranty on Water Heater & Parts
5. Lifetime Warranty on Workmanship
*All Warranties are Transferrable Upon Home Sale

Once design is selected and finalized, I need the website coded in a standard HTML/CSS and temporarily hosted on your development server so I can see the website functionality that is not observable from screenshots, such as section animations, etc. Once those details are finalized, I will move the source code to my server and complete the project.

Residential Home Owners and Business Owners

Plumbing, Home Services, Remodeling, Construction

0054AA
0677BA
7BADD7
CADEEF
E8F1F8
FFC000
F8CF3A
FAE287
FDF2CF
FEFAEE
EE7325
F08F49
F5BC92
FAE3D3
FDF4ED

• Clean, colorful, and professional

```html
<!DOCTYPE html>
<html lang="en">
<head>
<meta charset="utf-8">
<title>Tankless Water Heaters | Mr. FlowKettle</title>
<link href="https://fonts.googleapis.com/css2?family=Poppins:wght@400;500;600;700;800&family=Open+Sans:wght@400;600&display=swap" rel="stylesheet">
<style>
:root{
  --navy:#0a2456;
  --navy-deep:#071c45;
  --blue:#0054AA;
  --blue-2:#0677BA;
  --sky:#7BADD7;
  --ice:#E8F1F8;
  --yellow:#FFC000;
  --orange:#EE7325;
  --orange-soft:#FAE3D3;
  --cream:#FDF4ED;
  --ink:#1d2433;
  --muted:#5d6472;
  --white:#ffffff;
}
*{box-sizing:border-box;margin:0;padding:0}
html,body{width:1200px;height:2356px;overflow:hidden}
body{font-family:"Open Sans",Arial,sans-serif;color:var(--ink);background:var(--white);position:relative}
h1,h2,h3,h4,.nav a,.brand-name,.btn{font-family:"Poppins",Arial,sans-serif}

/* top bar */
.topbar{position:absolute;top:0;left:0;width:1200px;height:40px;background:var(--navy);color:#dfe8f5;font-size:13px}
.topbar .contact-row{position:absolute;right:120px;top:11px;display:flex;gap:30px}
.topbar span{display:flex;align-items:center;gap:7px}
.topbar svg{width:14px;height:14px}

/* header */
.site-header{position:absolute;top:40px;left:0;width:1200px;height:88px;background:var(--white);box-shadow:0 2px 10px rgba(0,0,0,.06);z-index:3}
.brand{position:absolute;left:120px;top:-30px;height:118px;display:flex;align-items:center;gap:10px}
.brand-mark{width:34px;height:34px;border-radius:50%;background:var(--orange)}
.brand-name{font-size:26px;font-weight:700;color:var(--blue)}
.nav{position:absolute;left:510px;top:32px;display:flex;gap:24px}
.nav a{font-size:13px;font-weight:600;color:var(--navy);text-decoration:none;letter-spacing:.3px}
.btn{position:absolute;right:120px;top:26px;background:var(--orange);color:var(--white);font-size:13px;font-weight:600;padding:10px 20px;border-radius:22px;display:flex;align-items:center;gap:8px}

/* hero */
.hero{position:absolute;top:128px;left:0;width:1200px;height:512px;overflow:hidden}
.hero-photo{position:absolute;inset:0;background:linear-gradient(90deg,#0a3a78 0%,#2a5d92 38%,#b9c3cc 62%,#e6e9ec 100%)}
.hero-shade{position:absolute;inset:0;background:linear-gradient(90deg,rgba(6,40,95,.85) 0%,rgba(6,40,95,.5) 40%,rgba(6,40,95,0) 65%)}
.hero h1{position:absolute;left:150px;top:112px;color:var(--white);font-size:56px;line-height:1.08;font-weight:700;letter-spacing:.5px}
.breadcrumb{position:absolute;left:150px;top:256px;color:#e9eef6;font-size:14px;display:flex;gap:8px}
.breadcrumb b{font-weight:600}
.hero-wave{position:absolute;left:0;bottom:0;width:1200px;height:150px}
.scroll-cue{position:absolute;left:578px;top:548px;width:44px;height:44px;border-radius:50%;background:var(--white);box-shadow:0 3px 10px rgba(0,0,0,.12);display:flex;align-items:center;justify-content:center;z-index:2}

/* intro */
.section-title{position:absolute;top:744px;left:0;width:1200px;text-align:center;font-size:36px;font-weight:700;color:var(--navy);letter-spacing:.3px}
.photo{position:absolute;border-radius:6px;box-shadow:0 8px 22px rgba(0,0,0,.15)}
.photo-tech{left:152px;top:948px;width:428px;height:412px;background:linear-gradient(135deg,#cfd6de 0%,#9aa8b8 45%,#4b5d74 100%)}
.feature-icon{position:absolute;left:612px;top:852px;width:56px;height:56px;border-radius:8px;background:var(--orange);display:flex;align-items:center;justify-content:center}
.intro-copy{position:absolute;left:612px;top:924px;width:452px;font-size:13px;line-height:1.75;color:var(--muted)}
.intro-copy p+p{margin-top:16px}

/* benefits band */
.benefit-band{position:absolute;left:0;top:1400px;width:1200px;height:420px;background:var(--cream)}
.benefit-copy{position:absolute;left:152px;top:1388px;width:480px;font-size:13px;line-height:1.75;color:var(--muted)}
.benefit-list{list-style:none;margin:18px 0}
.benefit-list li{display:flex;gap:10px;align-items:flex-start;font-weight:600;color:var(--ink);margin-bottom:8px}
.benefit-list svg{flex:0 0 18px;margin-top:3px}
.photo-repair{left:728px;top:1360px;width:332px;height:384px;background:linear-gradient(160deg,#6e4a2a 0%,#b07a3f 35%,#6b7a86 70%,#2e3a48 100%)}

/* footer */
.site-footer{position:absolute;left:0;top:1880px;width:1200px;height:476px;background:var(--navy-deep);color:#c9d4e6}
.footer-brand{position:absolute;left:152px;top:60px;display:flex;align-items:center;gap:10px}
.footer-brand .brand-name{color:var(--white)}
.follow{position:absolute;left:152px;top:206px}
.follow h4{color:var(--white);font-size:15px;font-weight:600;margin-bottom:14px}
.socials{display:flex;gap:10px}
.socials span{width:28px;height:28px;border-radius:50%;background:var(--orange)}
.footer-col{position:absolute;top:72px}
.footer-col h4{color:var(--white);font-size:16px;font-weight:600;margin-bottom:20px}
.footer-col li{list-style:none;font-size:13px;margin-bottom:14px}
.col-company{left:400px}
.col-legal{left:664px}
.col-contact{left:868px}
.contact-item{display:flex;gap:10px;align-items:flex-start;font-size:13px;margin-bottom:18px;line-height:1.5}
.contact-item i{flex:0 0 26px;height:26px;border-radius:50%;background:var(--orange);display:flex;align-items:center;justify-content:center}
.footer-rule{position:absolute;left:152px;right:152px;top:388px;height:1px;background:rgba(255,255,255,.15)}
.copyright{position:absolute;left:0;top:420px;width:1200px;text-align:center;font-size:12px;color:#9fb0cb}
</style>
</head>
<body>

<div class="topbar">
  <div class="contact-row">
    <span><svg viewBox="0 0 24 24" fill="#FFC000"><path d="M6.6 10.8a15.5 15.5 0 0 0 6.6 6.6l2.2-2.2a1 1 0 0 1 1-.25 11.4 11.4 0 0 0 3.6.57 1 1 0 0 1 1 1V20a1 1 0 0 1-1 1A17 17 0 0 1 3 4a1 1 0 0 1 1-1h3.5a1 1 0 0 1 1 1c0 1.25.2 2.45.57 3.57a1 1 0 0 1-.25 1z"/></svg>(561) 555-0142</span>
    <span><svg viewBox="0 0 24 24" fill="#FFC000"><path d="M3 5h18v14H3z" opacity=".0"/><path d="M2 5a1 1 0 0 1 1-1h18a1 1 0 0 1 1 1v14a1 1 0 0 1-1 1H3a1 1 0 0 1-1-1zm2 1.4V18h16V6.4l-8 5.6z"/></svg>Email: info@mrflowkettle.com</span>
  </div>
</div>

<header class="site-header">
  <div class="brand"><span class="brand-mark"></span><span class="brand-name">Mr. FlowKettle</span></div>
  <nav class="nav">
    <a>HOME</a><a>SERVICES</a><a>ABOUT</a><a>TESTIMONIALS</a><a>CONTACT</a>
  </nav>
  <div class="btn">GET QUOTE <svg width="12" height="12" viewBox="0 0 24 24" fill="none" stroke="#fff" stroke-width="3"><path d="M5 12h14M13 6l6 6-6 6"/></svg></div>
</header>

<section class="hero">
  <div class="hero-photo" role="img" aria-label="Wall-mounted white tankless water heater in a bright utility room"></div>
  <div class="hero-shade"></div>
  <h1>TANKLESS<br>WATER HEATERS</h1>
  <div class="breadcrumb"><span>Home</span><span>»</span><b>Tankless Water Heaters</b></div>
  <svg class="hero-wave" viewBox="0 0 1200 150" preserveAspectRatio="none">
    <path d="M0 70 C300 150 900 150 1200 60 L1200 150 L0 150Z" fill="#0677BA"/>
    <path d="M0 92 C300 160 900 160 1200 84 L1200 150 L0 150Z" fill="#ffffff"/>
  </svg>
</section>
<div class="scroll-cue"><svg width="14" height="22" viewBox="0 0 14 22" fill="none" stroke="#0054AA" stroke-width="2"><rect x="1" y="1" width="12" height="20" rx="6"/><path d="M7 5v4"/></svg></div>

<h2 class="section-title">TANKLESS WATER HEATERS</h2>

<div class="photo photo-tech" role="img" aria-label="Plumber in white hard hat servicing a tankless water heater"></div>
<div class="feature-icon"><svg width="30" height="30" viewBox="0 0 24 24" fill="none" stroke="#fff" stroke-width="2"><path d="M14.7 6.3a4 4 0 0 0-5.4 5.4L3 18l3 3 6.3-6.3a4 4 0 0 0 5.4-5.4l-2.5 2.5-2.4-.6-.6-2.4z"/></svg></div>
<div class="intro-copy">
  <p>Tankless heaters warm water only when you open a tap, so there is no tank to keep hot and no standby loss. Our licensed crews size each unit to your home, check gas and electric supply, and install it cleanly with proper venting. Most installs are finished the same day, and every job carries our Best Price Guarantee along with a full warranty on parts and labor.</p>
  <p>Switching from a standard tank frees up floor space and gives endless hot water for busy homes and businesses. We remove the old heater, haul it away, and walk you through the settings before we leave. Our team also handles yearly flushing and descaling so your unit runs at peak efficiency for many years to come.</p>
</div>

<div class="benefit-band"></div>
<div class="benefit-copy">
  <p>Choosing the right on-demand heater depends on flow rate, fuel type and how many fixtures run at once. We review your needs and recommend a model that balances comfort, running cost and price, with clear quotes and no hidden fees.</p>
  <ul class="benefit-list">
    <li><svg width="18" height="18" viewBox="0 0 24 24"><circle cx="12" cy="12" r="11" fill="#EE7325"/><path d="M7 12.5l3 3 7-7" stroke="#fff" stroke-width="2.5" fill="none"/></svg>Same-day service across Palm Beach County</li>
    <li><svg width="18" height="18" viewBox="0 0 24 24"><circle cx="12" cy="12" r="11" fill="#EE7325"/><path d="M7 12.5l3 3 7-7" stroke="#fff" stroke-width="2.5" fill="none"/></svg>15-year warranty on water heater and parts, plus lifetime warranty on workmanship</li>
    <li><svg width="18" height="18" viewBox="0 0 24 24"><circle cx="12" cy="12" r="11" fill="#EE7325"/><path d="M7 12.5l3 3 7-7" stroke="#fff" stroke-width="2.5" fill="none"/></svg>Best price guarantee on every install</li>
    <li><svg width="18" height="18" viewBox="0 0 24 24"><circle cx="12" cy="12" r="11" fill="#EE7325"/><path d="M7 12.5l3 3 7-7" stroke="#fff" stroke-width="2.5" fill="none"/></svg>100% satisfaction rating</li>
  </ul>
  <p>All warranties are transferable upon home sale, adding lasting value to your property and peace of mind for the next owner.</p>
</div>
<div class="photo photo-repair" role="img" aria-label="Hands tightening copper pipe fittings on a water heater"></div>

<footer class="site-footer">
  <div class="footer-brand"><span class="brand-mark"></span><span class="brand-name">Mr. FlowKettle</span></div>
  <div class="follow">
    <h4>Follow Us Now</h4>
    <div class="socials"><span></span><span></span><span></span></div>
  </div>
  <div class="footer-col col-company">
    <h4>Company</h4>
    <ul><li>Home</li><li>About Us</li><li>Gas Water Heaters</li><li>Electric Water Heaters</li><li>Tankless Water Heaters</li><li>Careers</li><li>Contact Us</li></ul>
  </div>
  <div class="footer-col col-legal">
    <h4>Legal Links</h4>
    <ul><li>Sitemap</li><li>Privacy Policy</li><li>Terms of Use</li></ul>
  </div>
  <div class="footer-col col-contact">
    <h4>Contact Us</h4>
    <div class="contact-item"><i><svg width="12" height="12" viewBox="0 0 24 24" fill="#fff"><path d="M6.6 10.8a15.5 15.5 0 0 0 6.6 6.6l2.2-2.2a1 1 0 0 1 1-.25 11.4 11.4 0 0 0 3.6.57 1 1 0 0 1 1 1V20a1 1 0 0 1-1 1A17 17 0 0 1 3 4a1 1 0 0 1 1-1h3.5a1 1 0 0 1 1 1c0 1.25.2 2.45.57 3.57a1 1 0 0 1-.25 1z"/></svg></i><span>(561) 555-0142</span></div>
    <div class="contact-item"><i><svg width="12" height="12" viewBox="0 0 24 24" fill="#fff"><path d="M2 5h20v14H2zm2 1.4V18h16V6.4l-8 5.6z"/></svg></i><span>info@mrflowkettle.com</span></div>
    <div class="contact-item"><i><svg width="12" height="12" viewBox="0 0 24 24" fill="#fff"><path d="M12 2a7 7 0 0 0-7 7c0 5 7 13 7 13s7-8 7-13a7 7 0 0 0-7-7zm0 9.5A2.5 2.5 0 1 1 12 6.5a2.5 2.5 0 0 1 0 5z"/></svg></i><span>4120 Harbor Point Ave,<br>Palm Beach County, FL 33401</span></div>
  </div>
  <div class="footer-rule"></div>
  <p class="copyright">© 2025 Mr. FlowKettle. All rights reserved.</p>
</footer>

</body>
</html>
```